Business Card Design

We need a business card designed for our new company. Prefer a black card with white logo & writing.

Contact Information for Business Card

Ted Galloway, address: 7-4812 Fernhollow Road, Abbotsford, BC, V3K 8R2, Office Phone: 604-712-3390, Cell: 604-947-2164, Email: ted@resinworkshub.ca

Colors

Designer to choose only greyscale colors for use in the design.

```html
<!DOCTYPE html>
<html lang="en">
<head>
<meta charset="utf-8">
<title>Resinworks Hub – Business Card</title>
<link href="https://fonts.googleapis.com/css2?family=Poppins:wght@300;400;600;700&display=swap" rel="stylesheet">
<style>
  :root {
    --backdrop: #1e1e1f;
    --card: #222226;
    --card-edge: #3a3a3e;
    --ink: #ffffff;
    --ink-soft: #d9d9d9;
    --rule: #8c8c8c;
    --band: #ffffff;
    --band-ink: #1c1c1c;
  }
  * { box-sizing: border-box; margin: 0; padding: 0; }
  html, body {
    width: 1200px; height: 711px; overflow: hidden;
    background: var(--backdrop);
    font-family: "Poppins", sans-serif;
  }
  .sheet {
    position: relative; width: 1200px; height: 711px;
    display: flex; align-items: center; justify-content: center; gap: 40px;
  }
  .card {
    position: relative; width: 540px; height: 310px;
    background: var(--card);
    border-radius: 18px;
    border: 1px solid var(--card-edge);
    overflow: hidden;
  }
  /* front */
  .card--front { display: flex; align-items: center; justify-content: center; }
  .brand-name {
    display: flex; align-items: center; gap: 14px;
    color: var(--ink); font-weight: 700; font-size: 34px; letter-spacing: 1px;
    text-transform: uppercase;
  }
  .brand-mark { width: 22px; height: 22px; background: var(--ink); }
  /* back */
  .brand-block {
    position: absolute; left: 30px; top: 80px; width: 200px; height: 110px;
    display: flex; align-items: center; justify-content: center;
  }
  .brand-block .brand-name { font-size: 21px; gap: 10px; }
  .brand-block .brand-mark { width: 14px; height: 14px; }
  .divider {
    position: absolute; left: 254px; top: 40px; width: 1px; height: 190px;
    background: var(--rule);
  }
  .person { position: absolute; left: 282px; top: 46px; color: var(--ink); }
  .person__name { font-size: 26px; line-height: 1.1; font-weight: 300; }
  .person__name strong { font-weight: 700; }
  .person__role { font-size: 12px; color: var(--ink-soft); margin-top: 2px; }
  .contacts { list-style: none; margin-top: 18px; }
  .contacts li {
    display: flex; align-items: center; gap: 10px;
    font-size: 12.5px; color: var(--ink); line-height: 1; margin-bottom: 9px;
  }
  .contacts svg { width: 13px; height: 13px; flex: none; }
  .accent {
    position: absolute; right: 0; top: 200px; width: 130px; height: 50px;
    background: linear-gradient(90deg, #6a6a6e, #d0d0d0);
    clip-path: polygon(30% 0, 100% 0, 100% 100%, 0 100%);
  }
  .address-band {
    position: absolute; left: 0; right: 0; bottom: 28px; height: 30px;
    background: var(--band); color: var(--band-ink);
    display: flex; align-items: center; justify-content: center;
    font-size: 14px; font-weight: 400; letter-spacing: 0.2px;
  }
</style>
</head>
<body>
<main class="sheet">
  <section class="card card--front" aria-label="Card front">
    <div class="brand-name"><span class="brand-mark"></span>Resinworks Hub</div>
  </section>

  <section class="card card--back" aria-label="Card back">
    <div class="brand-block">
      <div class="brand-name"><span class="brand-mark"></span>Resinworks Hub</div>
    </div>
    <div class="divider"></div>
    <div class="person">
      <h1 class="person__name"><strong>Ted</strong> Galloway</h1>
      <p class="person__role">Founder &amp; CEO</p>
      <ul class="contacts">
        <li>
          <svg viewBox="0 0 24 24" fill="none" stroke="#fff" stroke-width="2"><path d="M5 3h4l2 5-3 2a12 12 0 0 0 6 6l2-3 5 2v4a2 2 0 0 1-2 2A18 18 0 0 1 3 5a2 2 0 0 1 2-2z"/></svg>
          604-712-3390
        </li>
        <li>
          <svg viewBox="0 0 24 24" fill="none" stroke="#fff" stroke-width="2"><rect x="6" y="2" width="12" height="20" rx="2"/><circle cx="12" cy="18" r="1" fill="#fff"/></svg>
          604-947-2164
        </li>
        <li>
          <svg viewBox="0 0 24 24" fill="none" stroke="#fff" stroke-width="2"><circle cx="12" cy="12" r="10"/><path d="M2 12h20M12 2c3 3 3 17 0 20M12 2c-3 3-3 17 0 20"/></svg>
          www.resinworkshub.ca
        </li>
        <li>
          <svg viewBox="0 0 24 24" fill="none" stroke="#fff" stroke-width="2"><rect x="2" y="5" width="20" height="14" rx="1"/><path d="M2 6l10 7 10-7"/></svg>
          ted@resinworkshub.ca
        </li>
      </ul>
    </div>
    <div class="accent" role="img" aria-label="Grey layered accent shapes"></div>
    <p class="address-band">7-4812 Fernhollow Road, Abbotsford, BC, V3K 8R2.</p>
  </section>
</main>
</body>
</html>
```